U.S. Popcorn company needs business cards

We are a popcorn company that manufactures popcorn and sells it to grocery stores worldwide. Our theme is "Americana" and our logo is U.S. route 66 which is the most famous highway in the U.S.

We would like the design to be simple and to use both sides. On the back side we would like to see just the logo and website. The front would be normal details

Target Market(s)

Wholesalers, grocers and distributors

Industry/Entity Type

Manufacture

Contact Information for Business Card

Business name: Prairie Lantern Popcorn
Phone: +1 555 308 4726
Email: Dale@prairielanternpopcorn.com
website: www.prairielanternpopcorn.com
Tag Line: "POPular for a reason"
Name: Dale Whitcombe
Title: Founder/President

Requirements
Must have
• Either this design should be fun or clean and simple. I will let you show me your thougths.
Nice to have
• Anything that ties in the real Hwy Route 66.
• Colors might need to be red, white and blue incorporated.
Should not have
• Not be too busy.

```html
<!DOCTYPE html>
<html lang="en">
<head>
<meta charset="utf-8">
<title>Prairie Lantern Popcorn – Business Cards</title>
<link rel="stylesheet" href="https://fonts.googleapis.com/css2?family=Open+Sans:ital,wght@0,400;0,700;1,400&family=Questrial&display=swap">
<style>
  :root {
    --navy: #1c2f6b;
    --red: #d0211f;
    --paper: #fbfbfb;
    --backdrop: #e4e4e4;
    --ink: #1c2f6b;
  }
  * { box-sizing: border-box; margin: 0; padding: 0; }
  html, body {
    width: 1200px; height: 576px; overflow: hidden;
    background: var(--backdrop);
  }
  .stage { position: relative; width: 1200px; height: 576px; }
  .card {
    position: absolute; top: 138px;
    width: 486px; height: 294px;
    background: var(--paper);
    border-radius: 6px;
    overflow: hidden;
  }
  .card--back { left: 80px; width: 486px; }
  .card--front { left: 602px; width: 480px; }

  /* Back side */
  .brand-name {
    font-family: "Open Sans", sans-serif;
    font-weight: 700;
    color: var(--navy);
    text-align: center;
    line-height: 1.05;
  }
  .card--back .brand-name {
    position: absolute; left: 0; right: 0; top: 82px;
    font-size: 38px;
  }
  .back-web {
    position: absolute; left: 0; right: 0; top: 256px;
    display: flex; align-items: center; justify-content: center; gap: 10px;
    font-family: "Open Sans", sans-serif; font-weight: 700;
    font-size: 12px; color: var(--navy);
  }
  .back-web .rule { width: 56px; height: 2px; background: var(--navy); border-radius: 1px; }
  .back-web .accent { color: var(--red); }

  /* Front side */
  .holder { position: absolute; left: 22px; top: 22px; }
  .holder__name {
    font-family: "Open Sans", sans-serif; font-weight: 700;
    font-size: 17px; color: var(--red);
  }
  .holder__title {
    font-family: "Open Sans", sans-serif; font-style: italic;
    font-size: 11px; color: var(--navy); margin-top: 1px;
  }
  .tagline {
    position: absolute; right: 22px; top: 26px;
    font-family: "Questrial", sans-serif; font-size: 15px; color: var(--navy);
  }
  .tagline strong { font-family: "Open Sans", sans-serif; font-weight: 700; color: var(--red); }
  .contacts {
    position: absolute; left: 22px; top: 193px;
    list-style: none;
    font-family: "Questrial", sans-serif; font-size: 13px; color: var(--navy);
  }
  .contacts li { display: flex; align-items: center; gap: 12px; height: 17px; }
  .contacts svg { width: 11px; height: 11px; flex: none; }
  .card--front .brand-name {
    position: absolute; right: 22px; top: 158px; width: 150px;
    font-size: 24px;
  }
  .stripe { position: absolute; left: 0; bottom: 0; width: 480px; height: 11px; }
</style>
</head>
<body>
<main class="stage">
  <section class="card card--back" aria-label="Card back">
    <p class="brand-name">Prairie Lantern<br>Popcorn</p>
    <p class="back-web">
      <span class="rule"></span>
      <span>www.<span class="accent">prairielanternpopcorn</span>.com</span>
      <span class="rule"></span>
    </p>
  </section>

  <section class="card card--front" aria-label="Card front">
    <div class="holder">
      <p class="holder__name">Dale Whitcombe</p>
      <p class="holder__title">Founder/President</p>
    </div>
    <p class="tagline">"<strong>POP</strong>ular for a reason"</p>

    <ul class="contacts">
      <li>
        <svg viewBox="0 0 12 12" aria-hidden="true"><path fill="var(--red)" d="M1 4c0-2 2-3 5-3s5 1 5 3l-2 .5-.5-1.5h-5L3 4.5zM2.5 6h7l1 5h-9z"/><circle cx="6" cy="8.3" r="1.3" fill="#fff"/></svg>
        <span>+1 555 308 4726</span>
      </li>
      <li>
        <svg viewBox="0 0 12 12" aria-hidden="true"><rect x="0.5" y="2" width="11" height="8" fill="var(--red)"/><path d="M0.5 2l5.5 4.5L11.5 2" fill="none" stroke="#fff" stroke-width="1"/></svg>
        <span>Dale@prairielanternpopcorn.com</span>
      </li>
      <li>
        <svg viewBox="0 0 12 12" aria-hidden="true"><circle cx="6" cy="6" r="5.5" fill="var(--red)"/><path d="M0.5 6h11M6 0.5v11M2 3h8M2 9h8" stroke="#fff" stroke-width="0.8"/><ellipse cx="6" cy="6" rx="2.5" ry="5.5" fill="none" stroke="#fff" stroke-width="0.8"/></svg>
        <span>www.prairielanternpopcorn.com</span>
      </li>
    </ul>

    <p class="brand-name">Prairie Lantern<br>Popcorn</p>

    <svg class="stripe" viewBox="0 0 480 11" preserveAspectRatio="none" aria-hidden="true">
      <polygon points="0,0 372,0 361,11 0,11" fill="var(--navy)"/>
      <polygon points="377,0 480,0 480,11 366,11" fill="var(--red)"/>
    </svg>
  </section>
</main>
</body>
</html>
```